Southern Plantskills Academy needs a modern website that oozes professionalism

Our current website is boring and looks like everyone elses. We need a modern website that says we are the best at plant operator training. We use Brontovex and Hiraketo equipment for our training. We train all over Australia in Civil Construction, Mining and Quarrying. We want to be the "Go to" website for all plant operator training in Australia.

Industry/Entity Type

Heavy Machinery Training

Colors
0054AA
0677BA
7BADD7
CADEEF
E8F1F8
FFF300
FFF600
FEFA6F
FFFEC7
FFFEE8

```html
<!DOCTYPE html>
<html lang="en">
<head>
<meta charset="utf-8">
<title>Southern Plantskills Academy</title>
<link href="https://fonts.googleapis.com/css2?family=Chakra+Petch:wght@600;700&family=Poppins:wght@400;500;600&display=swap" rel="stylesheet">
<style>
:root{
  --blue:#0054aa;
  --blue-mid:#0677ba;
  --blue-soft:#7badd7;
  --blue-pale:#cadeef;
  --blue-mist:#e8f1f8;
  --yellow:#fff300;
  --yellow-soft:#fefa6f;
  --cream:#fffec7;
  --cream-light:#fffee8;
  --ink:#2b2b2b;
  --muted:#4a4a4a;
  --dark:#00346a;
  --white:#ffffff;
}
*{box-sizing:border-box;margin:0;padding:0}
html,body{width:1200px;height:4494px;overflow:hidden}
body{position:relative;background:var(--white);font-family:"Poppins",sans-serif;color:var(--ink)}
.abs{position:absolute}
.heading{font-family:"Chakra Petch",sans-serif;font-weight:700;text-transform:uppercase;color:var(--blue)}
.eyebrow{font-family:"Chakra Petch",sans-serif;font-weight:700;font-size:15px;text-transform:uppercase;color:var(--blue);letter-spacing:.3px}
.rule{position:absolute;height:2px;background:var(--yellow)}
.rule::before{content:"";position:absolute;left:50%;top:-2px;width:8px;height:6px;margin-left:-4px;background:var(--blue)}
.btn{position:absolute;display:flex;align-items:center;justify-content:center;font-family:"Chakra Petch",sans-serif;font-weight:700;font-size:16px;text-transform:uppercase}
.btn-blue{background:var(--blue);color:var(--white);box-shadow:0 0 0 2px var(--yellow)}

/* header */
.brand{left:108px;top:12px;height:64px;display:flex;align-items:center;gap:12px}
.brand-dot{width:44px;height:44px;border-radius:50%;background:var(--blue)}
.brand-name{font-family:"Chakra Petch",sans-serif;font-weight:700;font-size:19px;line-height:21px;color:var(--blue);width:240px}
.top-btn{top:19px;height:46px;font-size:16px}
.btn-calendar{left:473px;width:188px;background:var(--blue);color:var(--white)}
.btn-handbook{left:677px;width:207px;background:var(--yellow);color:var(--blue)}
.call{left:916px;top:16px;color:var(--blue)}
.call-label{font-family:"Chakra Petch",sans-serif;font-weight:700;font-size:16px;font-variant:small-caps}
.call-num{font-family:"Chakra Petch",sans-serif;font-weight:700;font-size:25px;line-height:30px}
.nav{left:0;top:91px;width:1200px;height:45px;background:var(--yellow);display:flex;align-items:center;justify-content:space-between;padding:0 28px 0 21px}
.nav a{font-family:"Chakra Petch",sans-serif;font-weight:700;font-size:14.5px;text-transform:uppercase;color:var(--blue);text-decoration:none}
.nav a.current{background:var(--blue);color:var(--white);padding:6px 12px;border-radius:16px}

/* hero */
.hero{left:0;top:136px;width:1200px;height:692px;overflow:hidden}
.hero-photo{position:absolute;inset:0;background:linear-gradient(100deg,#6b5a3e 0%,#8c7550 35%,#a88d5f 60%,#7d6846 100%)}
.hero-shade{position:absolute;inset:0;background:linear-gradient(90deg,rgba(40,30,15,.45),rgba(40,30,15,0) 60%)}
.hero-line{position:absolute;left:108px;font-family:"Chakra Petch",sans-serif;font-weight:700;font-size:50px;line-height:56px;color:var(--white);text-transform:uppercase}
.hero-mark{left:98px;top:211px;width:322px;height:68px;background:var(--yellow);color:var(--blue);padding-left:12px;display:flex;align-items:center}
.hero-btn{left:115px;top:370px;width:154px;height:43px;font-size:16px}
.dots{left:116px;top:441px;display:flex;gap:8px;align-items:center}
.dots span{width:12px;height:12px;border-radius:50%;border:2px solid var(--white)}
.dots span.on{width:17px;height:17px;background:var(--yellow);border-color:var(--yellow)}
.hero-curve{position:absolute;left:0;bottom:0}

/* about */
.about-photo{left:131px;top:930px;width:436px;height:436px;border-radius:50%;border:7px solid var(--yellow);background:radial-gradient(circle at 50% 40%,#c9a770,#8a6d45 60%,#5a4a38)}
.about-copy{left:607px;top:918px;width:481px}
.about-copy .title{font-size:42px;line-height:50px;margin-top:4px}
.about-mark{width:8px;height:6px;background:var(--blue);margin:10px 0 14px 4px}
.about-copy p{font-size:14px;line-height:24.6px;color:var(--muted);text-align:justify}
.about-btn{left:607px;top:1294px;width:152px;height:44px}

/* why */
.why{left:0;top:1448px;width:1200px;height:654px;background:var(--cream-light)}
.center{width:1200px;text-align:center;left:0}
.title-xl{font-size:42px;line-height:50px}
.why-text{left:157px;top:210px;width:886px;text-align:center;font-size:14.5px;line-height:25px;color:var(--muted)}
.point{position:absolute;top:305px;width:300px}
.point-icon{width:87px;height:87px;border-radius:50%;border:8px solid var(--yellow);border-right-color:transparent;display:flex;align-items:center;justify-content:center;font-family:"Chakra Petch",sans-serif;font-weight:700;font-size:30px;color:var(--blue);background:var(--white)}
.point h3{font-size:30px;line-height:33px;margin-top:44px}
.point p{font-size:14px;line-height:24px;color:var(--muted);margin-top:18px;width:270px}

/* courses */
.courses{left:0;top:2102px;width:1200px;height:698px;background:var(--blue)}
.courses .eyebrow,.courses .heading{color:var(--white)}
.card{position:absolute;top:212px;width:310px;height:363px;background:var(--white);clip-path:polygon(0 0,100% 0,100% 76.8%,236px 100%,0 100%)}
.card-photo{width:310px;height:279px}
.card h4{font-family:"Chakra Petch",sans-serif;font-weight:700;font-size:22px;color:var(--ink);margin:14px 0 0 16px}
.card .more{display:flex;align-items:center;gap:16px;margin:6px 0 0 16px;font-size:13px;color:var(--muted);text-decoration:underline}
.arrow-btn{position:absolute;top:362px;width:60px;height:60px;border-radius:50%;background:var(--yellow);display:flex;align-items:center;justify-content:center}

/* partner */
.partner-text{left:95px;top:3087px;width:410px;text-align:right;font-size:19px;line-height:31.5px;color:var(--muted)}
.partner-photo{left:537px;top:2982px;width:548px;height:412px;background:linear-gradient(120deg,#c8cdd3 0%,#9aa2a9 40%,#d59440 70%,#6f6250 100%)}

/* locations */
.locations{left:0;top:3480px;width:1200px;height:600px;background:var(--cream-light)}
.map{left:108px;top:87px;width:459px;height:371px;border:6px solid var(--yellow);background:linear-gradient(135deg,var(--blue-mist),#f3f1ea 55%,var(--blue-pale))}
.loc{left:656px;top:55px;width:520px}
.loc .title{font-size:42px;line-height:50px;margin-top:4px}
.loc-line{width:120px;height:2px;background:var(--yellow);margin-top:2px}
.loc p.lead{font-size:18px;line-height:31px;color:var(--muted);margin-top:16px}
.contact{position:absolute;left:0;display:flex;gap:20px;align-items:center}
.contact-icon{width:50px;height:50px;border-radius:50%;background:var(--blue);display:flex;align-items:center;justify-content:center}
.contact b{display:block;font-size:17px;font-weight:600;color:var(--ink);line-height:24px}
.contact span{font-size:17px;color:var(--muted);line-height:24px}

/* footer */
.footer{left:0;top:4064px;width:1200px;height:430px}
.footer-panel{position:absolute;left:549px;top:0;width:651px;height:430px;background:var(--dark)}
.footer-brand{left:131px;top:150px;display:flex;align-items:center;gap:14px}
.socials{left:231px;top:280px;display:flex;gap:16px}
.socials span{width:34px;height:34px;border-radius:50%;background:var(--yellow)}
.fcol{position:absolute;top:110px}
.fcol h5{font-family:"Chakra Petch",sans-serif;font-weight:700;font-size:18px;color:var(--white);text-transform:uppercase}
.fcol h5::after{content:"";display:block;width:44px;height:2px;background:var(--yellow);margin-top:8px}
.fcol ul{list-style:none;margin-top:20px}
.fcol li{font-size:12.5px;line-height:26px;color:var(--blue-pale)}
.footer-rule{left:108px;top:348px;width:1092px;height:1px;background:var(--blue-soft)}
.copy{left:574px;top:374px;font-size:13px;color:var(--white)}
</style>
</head>
<body>

<!-- header -->
<div class="abs brand"><span class="brand-dot"></span><span class="brand-name">Southern Plantskills Academy</span></div>
<div class="btn top-btn btn-calendar">Course Calendar</div>
<div class="btn top-btn btn-handbook">Student Handbook</div>
<div class="abs call"><div class="call-label">Call Us Today!</div><div class="call-num">1300 555 010</div></div>
<nav class="abs nav">
  <a class="current">Home</a><a>About Us</a><a>Courses</a><a>Onsite / Private Courses</a><a>Online Training</a><a>Our Services</a><a>Student Information</a>
</nav>

<!-- hero -->
<section class="abs hero">
  <div class="hero-photo" role="img" aria-label="Large haul truck driving through a dusty open-cut mine"></div>
  <div class="hero-shade"></div>
  <div class="hero-line" style="top:139px">Training and</div>
  <div class="hero-line hero-mark abs">Experience</div>
  <div class="hero-line" style="top:290px">You can rely on</div>
  <div class="btn btn-blue hero-btn">Get Started</div>
  <div class="abs dots"><span></span><span class="on"></span><span></span><span></span></div>
  <svg class="hero-curve" width="1200" height="140" viewBox="0 0 1200 140">
    <path d="M0 140 L0 70 C250 130 600 150 1200 40 L1200 140 Z" fill="#fff300"/>
    <path d="M620 140 C850 120 1050 90 1200 55 L1200 140 Z" fill="#0054aa"/>
    <path d="M0 140 L0 108 C300 150 700 150 1200 78 L1200 140 Z" fill="#ffffff"/>
  </svg>
</section>

<!-- about -->
<div class="abs about-photo" role="img" aria-label="Plant operator in hard hat and hi-vis vest seated at excavator controls"></div>
<div class="abs about-copy">
  <div class="eyebrow">About</div>
  <h2 class="heading title">Who We Are</h2>
  <div class="about-mark"></div>
  <p>Southern Plantskills Academy is a versatile team of passionate plant operator, safety and training professionals, all striving towards the common goal of achieving no harm to people, assets and the environment. Our experienced team have been training operators across Australia for over 10 years on modern Brontovex and Hiraketo equipment, with trainers based in every state. During this time we have built a solid reputation for thorough, timely and efficient training that is specifically tailored to meet the individual needs of our valued clients within Civil Construction, Mining and Quarrying.</p>
</div>
<div class="btn btn-blue about-btn">Learn More</div>

<!-- why -->
<section class="abs why">
  <div class="abs center eyebrow" style="top:94px">Why opt for us?</div>
  <h2 class="abs center heading title-xl" style="top:116px">Why Choose Us?</h2>
  <div class="rule" style="left:525px;top:174px;width:150px"></div>
  <p class="abs why-text">Southern Plantskills Academy trainers have come from the same industries that we train for. Our wealth of first hand knowledge and experience enables us to make invaluable contributions to all facets of plant operation, safety and training in your workplace.</p>
  <div class="point" style="left:110px"><div class="point-icon">1</div><h3 class="heading">We Are<br>Passionate</h3><p>We are passionate about safe plant operation.</p></div>
  <div class="point" style="left:492px"><div class="point-icon">2</div><h3 class="heading">We Are<br>Dependable</h3><p>Let us deliver the right training solution for your business.</p></div>
  <div class="point" style="left:849px"><div class="point-icon">3</div><h3 class="heading">Nationally<br>Recognised</h3><p>We are accredited to deliver nationally recognised training.</p></div>
</section>

<!-- courses -->
<section class="abs courses">
  <div class="abs center eyebrow" style="top:82px">Our Programs</div>
  <h2 class="abs center heading title-xl" style="top:104px">Our Courses</h2>
  <div class="rule" style="left:525px;top:160px;width:150px"></div>
  <div class="arrow-btn" style="left:40px"><svg width="26" height="18" viewBox="0 0 26 18"><path d="M25 9H2M9 1 1 9l8 8" stroke="#0054aa" stroke-width="2.4" fill="none"/></svg></div>
  <div class="card" style="left:112px"><div class="card-photo" role="img" aria-label="Smiling safety officer in hi-vis vest beside heavy machinery" style="background:linear-gradient(160deg,#9aa08c,#6e7a52 55%,#b0a27a)"></div><h4>Safety Training</h4><div class="more">Learn More <svg width="46" height="10" viewBox="0 0 46 10"><path d="M0 5h44M39 1l5 4-5 4" stroke="#0054aa" stroke-width="1.6" fill="none"/></svg></div></div>
  <div class="card" style="left:446px"><div class="card-photo" role="img" aria-label="Orange excavator loading a haul truck at a mine site" style="background:linear-gradient(170deg,#9fb0c0,#b9622e 50%,#6a5a4a)"></div><h4>Coal Mine Training</h4><div class="more">Learn More <svg width="46" height="10" viewBox="0 0 46 10"><path d="M0 5h44M39 1l5 4-5 4" stroke="#0054aa" stroke-width="1.6" fill="none"/></svg></div></div>
  <div class="card" style="left:778px"><div class="card-photo" role="img" aria-label="Two workers in hard hats and orange vests reviewing plans on site" style="background:linear-gradient(160deg,#3d3d3d,#d2762d 55%,#8a8176)"></div><h4>Plant Operator Training</h4><div class="more">Learn More <svg width="46" height="10" viewBox="0 0 46 10"><path d="M0 5h44M39 1l5 4-5 4" stroke="#0054aa" stroke-width="1.6" fill="none"/></svg></div></div>
  <div class="arrow-btn" style="left:1098px"><svg width="26" height="18" viewBox="0 0 26 18"><path d="M1 9h23M17 1l8 8-8 8" stroke="#0054aa" stroke-width="2.4" fill="none"/></svg></div>
</section>

<!-- partner -->
<div class="abs center eyebrow" style="top:2880px">Reliable Training Companion</div>
<h2 class="abs center heading title-xl" style="top:2902px">Your Trusted Training Partner</h2>
<div class="rule" style="left:525px;top:2958px;width:150px"></div>
<p class="abs partner-text">We assist our clients in their ongoing quest to achieve zero harm by providing them with the highest calibre of plant operator training and personalised safety advice.</p>
<div class="abs partner-photo" role="img" aria-label="Two engineers in hard hats inspecting machinery beside a yellow excavator"></div>

<!-- locations -->
<section class="abs locations">
  <div class="abs map" role="img" aria-label="Map of Australia marking the academy's training locations"></div>
  <div class="abs loc">
    <div class="eyebrow">Branches</div>
    <h2 class="heading title">Locations</h2>
    <div class="loc-line"></div>
    <p class="lead">We deliver training all over Australia, onsite at your worksite or at our training yards.</p>
  </div>
  <div class="contact abs" style="left:650px;top:245px">
    <div class="contact-icon"><svg width="22" height="22" viewBox="0 0 24 24"><path d="M6.6 10.8a15 15 0 0 0 6.6 6.6l2.2-2.2c.3-.3.7-.4 1-.2 1.1.4 2.3.6 3.6.6.6 0 1 .4 1 1V20c0 .6-.4 1-1 1A17 17 0 0 1 3 4c0-.6.4-1 1-1h3.5c.6 0 1 .4 1 1 0 1.3.2 2.5.6 3.6.1.3 0 .7-.2 1z" fill="#fff300"/></svg></div>
    <div><b>Call Us</b><span>1300 555 010</span></div>
  </div>
  <div class="contact abs" style="left:650px;top:323px">
    <div class="contact-icon"><svg width="22" height="16" viewBox="0 0 22 16"><rect x="0" y="0" width="22" height="16" rx="2" fill="#fff300"/><path d="M1 1l10 8 10-8" stroke="#0054aa" stroke-width="1.6" fill="none"/></svg></div>
    <div><b>Email</b><span>info@plantskillsacademy.com</span></div>
  </div>
  <div class="contact abs" style="left:650px;top:401px">
    <div class="contact-icon"><svg width="18" height="24" viewBox="0 0 18 24"><path d="M9 0a9 9 0 0 0-9 9c0 6.5 9 15 9 15s9-8.5 9-15a9 9 0 0 0-9-9zm0 12.5A3.5 3.5 0 1 1 9 5.5a3.5 3.5 0 0 1 0 7z" fill="#fff300"/></svg></div>
    <div><b>Training</b><span>Southern Plantskills Academy - RTO number #58214</span></div>
  </div>
</section>

<!-- footer -->
<footer class="abs footer">
  <div class="footer-panel"></div>
  <svg class="abs" style="left:0;top:-10px" width="1200" height="110" viewBox="0 0 1200 110">
    <path d="M0 10 L1200 10 L1200 0 L0 0 Z" fill="#fffee8"/>
    <path d="M0 10 L0 110 L549 110 L549 10 Z" fill="#fffee8"/>
    <path d="M549 10 C800 12 1000 30 1200 70 L1200 10 Z" fill="#fffee8"/>
    <path d="M0 110 L0 70 C250 30 550 20 760 28 C950 36 1100 60 1200 90 L1200 72 C1080 40 920 18 740 14 C500 10 250 30 0 58 Z" fill="#fff300"/>
    <path d="M700 14 C900 10 1080 25 1200 45 L1200 62 C1080 35 900 20 700 14 Z" fill="#0054aa"/>
  </svg>
  <div class="abs footer-brand"><span class="brand-dot"></span><span class="brand-name">Southern Plantskills Academy</span></div>
  <div class="abs socials"><span aria-label="Social profile"></span><span aria-label="Social profile"></span><span aria-label="Social profile"></span></div>
  <div class="fcol" style="left:582px"><h5>Quick Links</h5><ul><li>Home</li><li>About Us</li><li>Services</li><li>Testimonials</li><li>Blog</li><li>Contact Us</li></ul></div>
  <div class="fcol" style="left:780px"><h5>Links</h5><ul><li>Copyright</li><li>Terms of Use</li><li>Privacy Policy</li><li>Accessibility</li><li>Sitemap</li></ul></div>
  <div class="fcol" style="left:931px"><h5>Support</h5><ul><li>Team</li><li>About Us</li><li>Careers</li><li>Our Values</li></ul></div>
  <div class="abs footer-rule"></div>
  <div class="abs copy">©2024. All rights reserved.</div>
</footer>

</body>
</html>
```